Quiet Hollow is a cabin in Gatlinburg, Tennessee, near the Ferncrest Ridge National Park. When our cabin was built, there was one thing more important than any other--peace. The front of our cabin is surrounded by woods. It has a huge deck with a swing, Adirondack chairs, and a love seat for relaxation. The back deck has a hot tub, a large round glass table for cocktails or dinner, and because we left no stone unturned, we have a telescope for stargazing. There are two master suites, each have a private bath with a large jetted tub, seperate shower, flat screen TV, and a door that leads to the back deck.

Industry/Entity Type

Business

Contact Information for Business Card

Quiet Hollow Vacation Rentals, LLC
871 Belford Crest Pl.
Oakland, Ky 42159
Janet M. Pruitt, Owner/Manager
(270) 614.2087

```html
<!DOCTYPE html>
<html lang="en">
<head>
<meta charset="utf-8">
<title>Quiet Hollow Vacation Rentals – Business Cards</title>
<link rel="stylesheet" href="https://fonts.googleapis.com/css2?family=Source+Sans+3:wght@400;600;700&display=swap">
<style>
  :root {
    --backdrop: #d9d9d7;
    --card-black: #030303;
    --strip-black: #151515;
    --brand-blue: #1c3f94;
    --name-blue: #2a4fae;
    --brand-orange: #f7861c;
    --ink-white: #ffffff;
    --card-w: 700px;
    --card-h: 400px;
  }
  * { box-sizing: border-box; margin: 0; padding: 0; }
  html, body {
    width: 1200px; height: 900px; overflow: hidden;
    background: var(--backdrop);
    font-family: "Source Sans 3", "Myriad Pro", sans-serif;
  }
  .sheet {
    width: 1200px; height: 900px;
    display: flex; flex-direction: column; align-items: center; justify-content: center;
    gap: 40px;
  }
  .card {
    position: relative;
    width: var(--card-w); height: var(--card-h);
    background: var(--card-black);
    overflow: hidden;
    box-shadow: 0 6px 18px rgba(0,0,0,.18);
  }

  /* Brand side */
  .card--brand .brand-name {
    position: absolute; left: 0; right: 0; top: 150px;
    text-align: center; color: var(--ink-white);
    font-weight: 700; line-height: 1.05;
    text-transform: uppercase;
  }
  .card--brand .brand-name__main { display: block; font-size: 52px; letter-spacing: 3px; }
  .card--brand .brand-name__sub  { display: block; font-size: 21px; letter-spacing: .5px; }
  .card--brand .band-blue {
    position: absolute; left: 0; right: 0; bottom: 34px; height: 26px; background: var(--brand-blue);
  }
  .card--brand .band-orange {
    position: absolute; left: 0; right: 0; bottom: 26px; height: 8px; background: var(--brand-orange);
  }

  /* Contact side */
  .card--contact .brand-name {
    position: absolute; left: 54px; top: 92px;
    color: var(--name-blue); font-weight: 700; text-transform: uppercase; line-height: 1.05;
  }
  .card--contact .brand-name__main { display: block; font-size: 44px; letter-spacing: 2px; }
  .card--contact .brand-name__sub  { display: block; font-size: 18px; letter-spacing: .3px; }
  .holder {
    position: absolute; right: 48px; top: 70px; text-align right;
    text-align: right;
  }
  .holder__name { color: var(--name-blue); font-weight: 700; font-size: 24px; letter-spacing: .5px; }
  .holder__title { color: var(--brand-orange); font-weight: 600; font-size: 18px; }
  .contact-strip {
    position: absolute; left: 0; right: 0; top: 232px; height: 104px;
    background: var(--strip-black);
  }
  .contact {
    position: absolute; color: var(--brand-orange); font-size: 17px; font-weight: 600; line-height: 1.5;
  }
  .contact__row { display: flex; align-items: center; gap: 8px; }
  .contact svg { width: 13px; height: 13px; fill: var(--name-blue); flex: none; }
  .contact--address { left: 40px; top: 14px; }
  .contact--address .contact__indent { padding-left: 21px; }
  .contact--phones { left: 290px; top: 40px; }
  .contact--online { left: 470px; top: 42px; }
  .card--contact .band-orange {
    position: absolute; left: 0; right: 0; top: 336px; height: 8px; background: var(--brand-orange);
  }
  .card--contact .band-blue {
    position: absolute; left: 0; right: 0; top: 344px; bottom: 0; background: var(--brand-blue);
  }
</style>
</head>
<body>
<main class="sheet">

  <section class="card card--brand" aria-label="Card front">
    <h1 class="brand-name">
      <span class="brand-name__main">Quiet Hollow</span>
      <span class="brand-name__sub">Vacation Rentals, LLC</span>
    </h1>
    <div class="band-blue"></div>
    <div class="band-orange"></div>
  </section>

  <section class="card card--contact" aria-label="Card back">
    <h2 class="brand-name">
      <span class="brand-name__main">Quiet Hollow</span>
      <span class="brand-name__sub">Vacation Rentals, LLC</span>
    </h2>

    <div class="holder">
      <p class="holder__name">JANET M. PRUITT</p>
      <p class="holder__title">Owner/Manager</p>
    </div>

    <div class="contact-strip">
      <div class="contact contact--address">
        <p class="contact__row">
          <svg viewBox="0 0 12 16" aria-hidden="true"><path d="M6 0a6 6 0 0 0-6 6c0 4.5 6 10 6 10s6-5.5 6-10a6 6 0 0 0-6-6zm0 8.5A2.5 2.5 0 1 1 6 3.5a2.5 2.5 0 0 1 0 5z"/></svg>
          871 Belford Crest Pl.,
        </p>
        <p class="contact__indent">Oakland, Ky 42159</p>
      </div>

      <div class="contact contact--phones">
        <p class="contact__row">
          <svg viewBox="0 0 16 14" aria-hidden="true"><path d="M1 4C1 2 3 1 8 1s7 1 7 3v1h-4V3.8C10 3.3 9 3 8 3s-2 .3-3 .8V5H1zM3 6h10l1 7H2z"/></svg>
          (270) 614.2087
        </p>
      </div>

      <div class="contact contact--online">
        <p class="contact__row">
          <svg viewBox="0 0 16 12" aria-hidden="true"><path d="M0 0h16v12H0zm1.5 1.5L8 7l6.5-5.5z"/></svg>
          info@youremail.com
        </p>
        <p class="contact__row">
          <svg viewBox="0 0 16 16" aria-hidden="true"><path d="M6.5 9.5l3-3M5 7.5L3 9.5a2.5 2.5 0 0 0 3.5 3.5l2-2M11 8.5l2-2A2.5 2.5 0 0 0 9.5 3l-2 2" stroke="#2a4fae" stroke-width="2" fill="none" stroke-linecap="round"/></svg>
          www.website.com
        </p>
      </div>
    </div>

    <div class="band-orange"></div>
    <div class="band-blue"></div>
  </section>

</main>
</body>
</html>
```